Harbor Crest Holdings Corporate Showcase

Provide an attractive Corporate Website for a boutique Investment Company to showcase our activities and corporate interests.

Our Company works across a number of Sectors including

Real Estate
E-Commerce
Healthcare
Beauty & Personal Care
Technology
Resources

Lets keep the personality

Modern
Global
Sophisticated
Calm
Interesting

Lets keep the pages with MINIMAL Words
Lets use Photos/ Imagery to tell the story

We'll need a Banner Menu -
About Us
Expertise
Global Outlook
Sectors
Management
Media
Contact Us

Many thanks
Best wishes
Dennis.

Target Market(s)

Investors
Clients

Coding

Coded - Design and coding required

Number of Pages Required

5+ page

Font styles to use
Sans Serif

Colors
886aae
3176b5
00a990
f68e4d
f04a50
e667a6

Requirements
Must have
• WordPress Coding

Checkout this Website for look and feel - its cool:
www.qvr-example.com

Harbor Crest Partners
(Harbor Crest Holdings LLP)
London
E9 4ZX
United Kingdom

www.HarborCrestPartners-example.com
Nice to have
• Sophisticated colour palette - black/ brown/ blue/ purple/

```html
<!DOCTYPE html>
<html lang="en">
<head>
<meta charset="utf-8">
<title>Harbor Crest Partners</title>
<link href="https://fonts.googleapis.com/css2?family=League+Spartan:wght@300;400;600;700&family=Raleway:wght@400;500;600;700&display=swap" rel="stylesheet">
<style>
:root{
  --red:#f04a50;
  --ink:#231f20;
  --dark:#1d1b1c;
  --text:#6d6d6d;
  --heading:#1e1e1e;
  --white:#ffffff;
  --line:#d9d9d9;
}
*{box-sizing:border-box;margin:0;padding:0}
html,body{width:1200px;height:4465px;overflow:hidden}
body{font-family:"Raleway",sans-serif;color:var(--text);background:var(--white);position:relative}
.abs{position:absolute}
h1,h2,h3,h4,.display{font-family:"League Spartan",sans-serif;color:var(--heading)}
.eyebrow{font-family:"League Spartan",sans-serif;color:var(--red);font-size:12px;letter-spacing:2px;text-transform:uppercase;font-weight:500}
.btn{display:flex;align-items:center;justify-content:center;font-family:"League Spartan",sans-serif;font-size:11.5px;font-weight:600;letter-spacing:3px;text-transform:uppercase;color:var(--white);background:var(--ink)}
.btn-red{background:var(--red)}
.dot{display:inline-block;width:14px;height:14px;border-radius:50%;background:currentColor}
p{line-height:24px;font-size:12.5px}

/* hero */
.hero{left:0;top:0;width:1200px;height:638px;background:radial-gradient(ellipse at 62% 55%,#4f6fa3 0%,#2e4674 35%,#1f2d4c 70%,#182238 100%)}
.hero-photo{left:0;top:0;width:1200px;height:638px}
.brand{left:94px;top:28px;font-family:"League Spartan",sans-serif;font-weight:700;font-size:25px;color:var(--white);letter-spacing:.2px}
.nav{right:88px;top:33px;display:flex;gap:28px;font-size:11.5px;color:var(--white);font-weight:500}
.nav-rule{left:94px;top:78px;width:1018px;height:1px;background:rgba(255,255,255,.25)}
.hero-kicker{left:0;width:1200px;top:262px;text-align:center;font-family:"League Spartan",sans-serif;font-weight:300;font-size:29px;color:var(--white)}
.hero-title{left:0;width:1200px;top:298px;text-align:center;font-family:"League Spartan",sans-serif;font-weight:700;font-size:48px;color:var(--white)}
.hero-btn{left:521px;top:375px;width:157px;height:39px}
.hero-social{left:94px;top:595px;display:flex;gap:24px;color:var(--white)}
.hero-social .dot{width:12px;height:12px}
.scroll{left:0;width:1200px;top:596px;text-align:center;font-family:"League Spartan",sans-serif;font-size:11px;letter-spacing:3px;color:var(--white)}
.scroll-line{left:599px;top:618px;width:2px;height:42px;background:var(--red)}

/* about */
.frame{border:2px solid var(--red)}
.about-photo-a{left:94px;top:664px;width:283px;height:358px;background:linear-gradient(135deg,#b9b2aa,#6f6a66 55%,#3e3d40)}
.about-photo-b{left:352px;top:748px;width:284px;height:358px;background:linear-gradient(160deg,#c9c6c2,#7a655a 50%,#2a2a2f);border-left:12px solid var(--white);border-top:12px solid var(--white)}
.about-text{left:700px;top:732px;width:345px}
.about-text h2{font-size:29px;font-weight:700;margin:14px 0 16px}
.about-btn{left:700px;top:994px;width:145px;height:43px}

/* sectors */
.sectors{left:0;top:1184px;width:1200px;height:446px;background:var(--dark)}
.sector{top:106px;width:200px;color:#dcdcdc}
.sector svg{display:block;margin-bottom:30px}
.sector h3{color:var(--white);font-size:15px;font-weight:700;margin-bottom:8px}
.sector p{font-size:12px;line-height:19px;color:#d0d0d0}
.sector-rule{top:90px;width:1px;height:270px;background:linear-gradient(#1d1b1c,#3a3738,#1d1b1c)}

/* blog */
.section-head{left:0;width:1200px;text-align:center}
.section-head h2{font-size:29px;font-weight:700;margin-top:8px}
.post-photo{width:506px;height:355px}
.post{width:450px}
.post .meta{font-family:"League Spartan",sans-serif;font-size:10.5px;color:var(--red);font-weight:500}
.post .meta b{color:var(--red);font-weight:600}
.post .meta span{color:var(--text)}
.post h3{font-family:"Raleway",sans-serif;font-weight:500;font-size:24px;margin:10px 0 14px;color:#222}
.post p{font-size:11.5px;line-height:25.5px}
.post .btn{width:144px;height:41px;margin-top:24px}
.view-all{left:509px;top:2878px;width:182px;height:43px;border:2px solid #3a3a3a;color:var(--ink);background:var(--white)}

/* media */
.media{left:0;top:2975px;width:1200px;height:585px;background:linear-gradient(180deg,#262426 0%,#1b1a1c 45%,#2a2829 100%)}
.media .section-head h2{color:var(--white)}
.media-card{top:148px;width:235px;height:357px;background:var(--white);padding:7px}
.media-card .thumb{width:221px;height:167px}
.media-card h4{font-size:15px;font-weight:700;margin:18px 0 6px 1px}
.media-card p{font-size:11.5px;line-height:19px}
.media-card .more{font-size:10.5px;color:var(--red);font-weight:600;margin-top:12px;display:block}
.arrow{top:522px;width:32px;height:32px;display:flex;align-items:center;justify-content:center}

/* contact */
.contact-box{left:149px;top:3699px;width:957px;height:341px;background:var(--white);box-shadow:0 6px 28px rgba(0,0,0,.14)}
.contact-panel{left:94px;top:3728px;width:306px;height:291px;background:var(--red);color:var(--white);padding:34px 16px}
.contact-panel h4{font-family:"Raleway",sans-serif;color:var(--white);font-size:18px;font-weight:600;letter-spacing:.5px;margin-bottom:14px}
.contact-row{display:flex;gap:10px;font-size:12.5px;line-height:20px;margin-bottom:10px}
.contact-row svg{flex:none;margin-top:3px}
.follow{font-size:13px;font-weight:600;margin:14px 0 16px}
.panel-social{display:flex;gap:16px}
.panel-social .dot{width:10px;height:10px}
.field{border:1px solid #cfcfcf;border-radius:3px;font-size:11.5px;color:#8a8a8a;padding:10px 7px}
.send{left:444px;top:3990px;width:144px;height:40px}

/* footer */
.footer{left:0;top:4097px;width:1200px;height:368px;background:var(--dark);color:#cfcfcf}
.footer h4{font-family:"Raleway",sans-serif;color:var(--white);font-size:14.5px;font-weight:500;line-height:18px}
.footer ul{list-style:none;font-size:12px;line-height:14px}
.footer .links li{margin-bottom:21px}
.footer .sector-list li{margin-bottom:12px}
.footer li:last-child{margin-bottom:0}
.foot-social{display:flex;gap:26px;color:var(--white)}
.foot-input{width:256px;height:36px;background:var(--white);font-size:11px;color:#777;padding:11px 12px}
.subscribe{width:128px;height:36px}
.foot-rule{left:94px;top:4403px;width:1012px;height:1px;background:#3b393a}
.copyright{left:0;width:1200px;top:4423px;text-align:center;font-size:11.5px;color:#9a9a9a}
.copyright span{color:var(--red)}
</style>
</head>
<body>

<!-- Hero -->
<header class="abs hero">
  <div class="abs hero-photo" role="img" aria-label="Business handshake overlaid with a glowing blue global network and financial chart"></div>
  <div class="abs brand">HARBOR CREST PARTNERS</div>
  <nav class="abs nav"><span>About Us</span><span>Expertise</span><span>Global Outlook</span><span>Sectors</span><span>Management</span><span>Media</span><span>Contact Us</span></nav>
  <div class="abs nav-rule"></div>
  <div class="abs hero-kicker">OUR COMPANY WORKS ACROSS</div>
  <h1 class="abs hero-title" style="color:var(--white)">A NUMBER OF SECTORS</h1>
  <div class="abs btn btn-red hero-btn">Know More</div>
  <div class="abs hero-social"><i class="dot"></i><i class="dot"></i><i class="dot"></i><i class="dot"></i></div>
  <div class="abs scroll">SCROLL DOWN</div>
  <div class="abs scroll-line"></div>
</header>

<!-- About -->
<div class="abs frame" style="left:300px;top:693px;width:234px;height:200px"></div>
<div class="abs frame" style="left:163px;top:880px;width:240px;height:198px"></div>
<div class="abs about-photo-a" role="img" aria-label="Close-up of two business people shaking hands"></div>
<div class="abs about-photo-b" role="img" aria-label="Two colleagues in business attire reviewing a tablet"></div>
<section class="abs about-text">
  <div class="eyebrow">About Us</div>
  <h2>A FEW WORDS ABOUT US</h2>
  <p>Lorem ipsum dolor sit amet, consectetur adipcing elit. Etiam et eros vel ligula malesuada aliquet at quis nunc. Etiam id erat ac libero hendrerit porta. Duis consectetur, tortor ac bibendum condimentum, dolor mi sodales ex, id suscipit mi elit ut odio. Orci varius natoque penatibus et magnis dis parturient montes, nascetur ridiculus mus. Proin quam augue</p>
</section>
<div class="abs btn about-btn">Read More</div>

<!-- Sectors -->
<section class="abs sectors">
  <div class="abs sector-rule" style="left:313px"></div>
  <div class="abs sector-rule" style="left:587px"></div>
  <div class="abs sector-rule" style="left:858px"></div>

  <div class="abs sector" style="left:94px">
    <svg width="88" height="86" viewBox="0 0 88 86"><rect x="6" y="6" width="80" height="78" rx="10" fill="#fff" opacity=".9"/><rect x="0" y="0" width="80" height="78" rx="10" fill="var(--red)"/><g fill="none" stroke="#fff" stroke-width="2.5"><rect x="26" y="16" width="28" height="48"/><path d="M20 64h40M32 24h4M44 24h4M32 32h4M44 32h4M32 40h4M44 40h4M32 48h4M44 48h4"/></g></svg>
    <h3>REAL ESTATE</h3>
    <p>Lorem ipsum dolor sit amet, cosectetur adipicing elit. Etiam et eros vel ligula malesuada aliquet at quis nunc.</p>
  </div>
  <div class="abs sector" style="left:365px">
    <svg width="88" height="86" viewBox="0 0 88 86"><rect x="6" y="6" width="80" height="78" rx="10" fill="#fff" opacity=".9"/><rect x="0" y="0" width="80" height="78" rx="10" fill="var(--red)"/><g fill="none" stroke="#fff" stroke-width="2.5"><path d="M20 24h8l6 22h20l5-16H30"/><circle cx="36" cy="54" r="3"/><circle cx="52" cy="54" r="3"/></g></svg>
    <h3>E-COMMERCE</h3>
    <p>Lorem ipsum dolor sit amet, cosectetur adipicing elit. Etiam et eros vel ligula malesuada aliquet at quis nunc.</p>
  </div>
  <div class="abs sector" style="left:635px">
    <svg width="88" height="86" viewBox="0 0 88 86"><rect x="6" y="6" width="80" height="78" rx="10" fill="#fff" opacity=".9"/><rect x="0" y="0" width="80" height="78" rx="10" fill="var(--red)"/><g fill="none" stroke="#fff" stroke-width="2.5"><path d="M40 52c-14-9-18-16-14-22 3-5 10-4 14 2 4-6 11-7 14-2 4 6 0 13-14 22z"/><path d="M40 32v12M34 38h12"/><path d="M20 54l12 10h16l12-10"/></g></svg>
    <h3>HEALTHCARE</h3>
    <p>Lorem ipsum dolor sit amet, cosectetur adipicing elit. Etiam et eros vel ligula malesuada aliquet at quis nunc.</p>
  </div>
  <div class="abs sector" style="left:908px">
    <svg width="88" height="86" viewBox="0 0 88 86"><rect x="6" y="6" width="80" height="78" rx="10" fill="#fff" opacity=".9"/><rect x="0" y="0" width="80" height="78" rx="10" fill="var(--red)"/><g fill="none" stroke="#fff" stroke-width="2.5"><rect x="30" y="40" width="20" height="22"/><path d="M34 40v-8h12v8M38 32v-8h4v8M22 62h36"/><circle cx="56" cy="24" r="4"/></g></svg>
    <h3>BEAUTY &amp; PERSONAL CARE</h3>
    <p>Lorem ipsum dolor sit amet, cosectetur adipicing elit. Etiam et eros vel ligula malesuada aliquet at quis nunc.</p>
  </div>
</section>

<!-- Blog -->
<div class="abs section-head" style="top:1683px">
  <div class="eyebrow">Blog</div>
  <h2>LATEST BLOG POSTS</h2>
</div>

<div class="abs post-photo" style="left:94px;top:1774px;background:linear-gradient(135deg,#e6e8ea,#b7bcc2 50%,#5d6067)" role="img" aria-label="Team gathered around a white meeting table reviewing charts"></div>
<article class="abs post" style="left:628px;top:1834px">
  <div class="meta"><b>DEC. 10, 2020</b> &nbsp;|&nbsp; POSTED BY <span>LOREM</span></div>
  <h3>Vestibulum vel dolor sed lacus lobortis</h3>
  <p>Phasellus dapibus tincidunt diam in convallis. Nam ac augue sem. Maecenas consectetur magna eget urna eleifend accumsan. Vivamus interdum ut tortor non sodales. Integer egestas dictum nunc et pharetra. Quisque a luctus mauris. Phasellus nec pretium nisi.</p>
  <div class="btn">Read More</div>
</article>

<article class="abs post" style="left:94px;top:2189px">
  <div class="meta"><b>DEC. 10, 2020</b> &nbsp;|&nbsp; POSTED BY <span>LOREM</span></div>
  <h3>Vestibulum vel dolor sed lacus lobortis</h3>
  <p>Phasellus dapibus tincidunt diam in convallis. Nam ac augue sem. Maecenas consectetur magna eget urna eleifend accumsan. Vivamus interdum ut tortor non sodales. Integer egestas dictum nunc et pharetra. Quisque a luctus mauris. Phasellus nec pretium nisi.</p>
  <div class="btn">Read More</div>
</article>
<div class="abs post-photo" style="left:601px;top:2129px;background:linear-gradient(135deg,#9fb4c4,#d8d2c8 45%,#b89a78)" role="img" aria-label="Hand with a pen working on a calculator beside an open notebook"></div>

<div class="abs post-photo" style="left:94px;top:2485px;background:linear-gradient(135deg,#c9c3ba,#8f8a85 45%,#4f5560)" role="img" aria-label="Woman working on a laptop in a busy office"></div>
<article class="abs post" style="left:628px;top:2545px">
  <div class="meta"><b>DEC. 10, 2020</b> &nbsp;|&nbsp; POSTED BY <span>LOREM</span></div>
  <h3>Vestibulum vel dolor sed lacus lobortis</h3>
  <p>Phasellus dapibus tincidunt diam in convallis. Nam ac augue sem. Maecenas consectetur magna eget urna eleifend accumsan. Vivamus interdum ut tortor non sodales. Integer egestas dictum nunc et pharetra. Quisque a luctus mauris. Phasellus nec pretium nisi.</p>
  <div class="btn">Read More</div>
</article>

<div class="abs btn view-all">View All Blog</div>

<!-- Media -->
<section class="abs media" role="img" aria-label="Dark city skyline backdrop">
  <div class="abs section-head" style="top:62px">
    <div class="eyebrow">Media</div>
    <h2>OUR MEDIA</h2>
  </div>
  <div class="abs media-card" style="left:94px">
    <div class="thumb" style="background:linear-gradient(135deg,#e3e1de,#b79b82 55%,#6c5a4c)" role="img" aria-label="Hands joining two puzzle pieces"></div>
    <h4>DONEC PEDE JUSTO</h4>
    <p>Lorem ipsum dolor sit a onsectetuer adipiscing elit. Aen commodo ligula eget dolor. Aenean massa. Cum sociis natoque penatibus et magnis dis parturient</p>
    <span class="more">Read More</span>
  </div>
  <div class="abs media-card" style="left:353px">
    <div class="thumb" style="background:linear-gradient(135deg,#e9ecee,#9aa3aa 55%,#2e3136)" role="img" aria-label="Businessman in a dark suit in a bright office"></div>
    <h4>DONEC PEDE JUSTO</h4>
    <p>Lorem ipsum dolor sit a onsectetuer adipiscing elit. Aen commodo ligula eget dolor. Aenean massa. Cum sociis natoque penatibus et magnis dis parturient</p>
    <span class="more">Read More</span>
  </div>
  <div class="abs media-card" style="left:612px">
    <div class="thumb" style="background:linear-gradient(135deg,#eef0f1,#b9bec2 55%,#3a3d42)" role="img" aria-label="Businessman at a desk reviewing documents"></div>
    <h4>DONEC PEDE JUSTO</h4>
    <p>Lorem ipsum dolor sit a onsectetuer adipiscing elit. Aen commodo ligula eget dolor. Aenean massa. Cum sociis natoque penatibus et magnis dis parturient</p>
    <span class="more">Read More</span>
  </div>
  <div class="abs media-card" style="left:871px">
    <div class="thumb" style="background:linear-gradient(135deg,#eceae6,#c7b7a3 55%,#8a7560)" role="img" aria-label="Businesswoman in a beige blazer in an office"></div>
    <h4>DONEC PEDE JUSTO</h4>
    <p>Lorem ipsum dolor sit a onsectetuer adipiscing elit. Aen commodo ligula eget dolor. Aenean massa. Cum sociis natoque penatibus et magnis dis parturient</p>
    <span class="more">Read More</span>
  </div>
  <div class="abs arrow" style="left:568px;background:#2b292a;border:1px solid #777"><svg width="10" height="14" viewBox="0 0 10 14"><path d="M8 1L2 7l6 6" fill="none" stroke="#fff" stroke-width="1.6"/></svg></div>
  <div class="abs arrow" style="left:600px;background:var(--red)"><svg width="10" height="14" viewBox="0 0 10 14"><path d="M2 1l6 6-6 6" fill="none" stroke="#fff" stroke-width="1.6"/></svg></div>
</section>

<!-- Contact -->
<div class="abs section-head" style="top:3613px">
  <div class="eyebrow">Contact Us</div>
  <h2>GET IN TOUCH</h2>
</div>
<div class="abs contact-box"></div>
<aside class="abs contact-panel">
  <h4>Contact Us</h4>
  <div class="contact-row"><svg width="14" height="16" viewBox="0 0 14 16"><path d="M7 15s5-5 5-9A5 5 0 0 0 2 6c0 4 5 9 5 9z" fill="none" stroke="#fff" stroke-width="1.8"/><circle cx="7" cy="6" r="1.8" fill="#fff"/></svg><span>45 Bay Court, Harbourside<br>Sydney, Australia</span></div>
  <div class="contact-row"><svg width="14" height="14" viewBox="0 0 14 14"><path d="M3 1l3 3-2 2c1 2 2 3 4 4l2-2 3 3-2 2C6 13 1 8 1 3z" fill="#fff"/></svg><span>01-555-0100-22</span></div>
  <div class="contact-row"><svg width="14" height="12" viewBox="0 0 14 12"><rect x="1" y="1" width="12" height="10" fill="none" stroke="#fff" stroke-width="1.6"/><path d="M1 1l6 5 6-5" fill="none" stroke="#fff" stroke-width="1.6"/></svg><span>info@harborcrestpartners-example.com</span></div>
  <div class="follow">Follow Us</div>
  <div class="panel-social"><i class="dot"></i><i class="dot"></i><i class="dot"></i><i class="dot"></i></div>
</aside>
<div class="abs field" style="left:444px;top:3758px;width:292px;height:36px">First Name</div>
<div class="abs field" style="left:744px;top:3758px;width:292px;height:36px">Last Name</div>
<div class="abs field" style="left:444px;top:3805px;width:292px;height:36px">Email address</div>
<div class="abs field" style="left:744px;top:3805px;width:292px;height:36px">Phone</div>
<div class="abs field" style="left:444px;top:3852px;width:592px;height:110px">Message</div>
<div class="abs btn btn-red send">Send Now</div>

<!-- Footer -->
<footer class="abs footer">
  <div class="abs" style="left:94px;top:80px"><h4>Follow Us</h4>
    <div class="foot-social" style="margin-top:22px"><i class="dot" style="width:12px;height:12px"></i><i class="dot" style="width:12px;height:12px"></i><i class="dot" style="width:12px;height:12px"></i><i class="dot" style="width:12px;height:12px"></i></div>
  </div>
  <div class="abs" style="left:340px;top:80px"><h4>Quick Links</h4>
    <div style="display:flex;gap:70px;margin-top:31px">
      <ul class="links"><li>About Us</li><li>Expertise</li><li>Global Outlook</li><li>Sectors</li></ul>
      <ul class="links"><li>Management</li><li>Media</li><li>Contact Us</li></ul>
    </div>
  </div>
  <div class="abs" style="left:653px;top:80px"><h4>Sectors</h4>
    <ul class="sector-list" style="margin-top:31px"><li>Real Estate</li><li>E-Commerce</li><li>Healthcare</li><li>Beauty &amp; Personal Care</li><li>Technology</li><li>Resources</li></ul>
  </div>
  <div class="abs" style="left:860px;top:80px">
    <h4 style="display:flex;align-items:center;gap:8px;font-size:12.5px"><svg width="14" height="10" viewBox="0 0 14 10"><rect x="1" y="1" width="12" height="8" fill="none" stroke="#fff" stroke-width="1.4"/><path d="M1 1l6 4 6-4" fill="none" stroke="#fff" stroke-width="1.4"/></svg>Stay update with us</h4>
    <div class="foot-input" style="margin-top:20px">Enter your Email address</div>
    <div class="btn btn-red subscribe" style="margin:14px 0 0 118px">Subscribe</div>
  </div>
</footer>
<div class="abs foot-rule"></div>
<div class="abs copyright">© 2020 <span>Harbor Crest Partners</span>. All Right Reserved.</div>

</body>
</html>
```